Tech business card design

We need an amazing business card design for our new business 'Pexla' a marketing tech startup based in Sydney, Australia. We provide an online marketplace for businesses to search and buy advertising media, connect with service providers and learn more about marketing. We wish to communicate 'cool tech', reliability and professionalism and design based around our logo.

Target Market(s)

Business Owners

Contact Information for Business Card

Name
Position
Email Address
Website
Phone Number

Font styles to use
Other font styles liked:
• Avenir & Avenir Next

Colors

Designer to choose colors to be used in the design.

```html
<!DOCTYPE html>
<html lang="en">
<head>
<meta charset="utf-8">
<title>Pexla Business Card</title>
<link rel="stylesheet" href="https://fonts.googleapis.com/css2?family=Roboto:wght@400;500;700;900&display=swap">
<style>
  :root {
    --backdrop: #1c1c44;
    --card-top: #1c1a58;
    --card-bottom: #141342;
    --ink: #ffffff;
    --ink-soft: #e6e6f2;
    --pattern-tone: #2a2a62;
  }
  * { margin: 0; padding: 0; box-sizing: border-box; }
  html, body {
    width: 1200px;
    height: 869px;
    overflow: hidden;
    background: var(--backdrop);
    font-family: "Roboto", Arial, sans-serif;
  }
  .canvas {
    position: relative;
    width: 1200px;
    height: 869px;
    background: var(--backdrop);
  }
  .card {
    position: absolute;
    top: 208px;
    width: 295px;
    height: 518px;
    background: linear-gradient(180deg, var(--card-top) 0%, var(--card-bottom) 100%);
    color: var(--ink);
    overflow: hidden;
  }
  .card--front { left: 266px; }
  .card--back  { left: 640px; }

  .wordmark {
    position: absolute;
    font-weight: 900;
    color: var(--ink);
    letter-spacing: -1px;
    line-height: 1;
  }
  .card--front .wordmark {
    top: 98px;
    left: 0;
    width: 100%;
    text-align: center;
    font-size: 76px;
  }
  .holder {
    position: absolute;
    top: 290px;
    width: 100%;
    text-align: center;
  }
  .holder__name {
    font-size: 21px;
    font-weight: 700;
    line-height: 1.1;
  }
  .holder__role {
    font-size: 13px;
    font-weight: 400;
    color: var(--ink-soft);
    margin-top: 2px;
  }
  .contact {
    position: absolute;
    top: 385px;
    width: 100%;
    text-align: center;
  }
  .contact__icons {
    display: flex;
    justify-content: center;
    gap: 4px;
    margin-bottom: 6px;
  }
  .contact__line {
    font-size: 12.5px;
    line-height: 17.5px;
    color: var(--ink-soft);
  }

  .back-texture {
    position: absolute;
    inset: 0;
    background:
      repeating-linear-gradient(-45deg, transparent 0 34px, rgba(255,255,255,0.04) 34px 58px),
      linear-gradient(180deg, var(--pattern-tone) 0%, var(--card-bottom) 100%);
  }
  .card--back .wordmark {
    right: 26px;
    bottom: 60px;
    font-size: 40px;
  }
</style>
</head>
<body>
<main class="canvas">
  <section class="card card--front">
    <div class="wordmark">pexla</div>

    <div class="holder">
      <p class="holder__name">Marcus Delane</p>
      <p class="holder__role">Managing Director</p>
    </div>

    <div class="contact">
      <div class="contact__icons">
        <svg width="16" height="16" viewBox="0 0 16 16" aria-label="phone">
          <circle cx="8" cy="8" r="8" fill="#fff"/>
          <path d="M5 4.5c.5-.4 1-.4 1.3 0l.8 1.2c.2.4.1.8-.2 1l-.5.4c.4.9 1 1.5 1.9 1.9l.4-.5c.3-.3.7-.4 1-.2l1.2.8c.4.3.4.8 0 1.3-.6.6-1.4.8-2.2.4C7 10.1 5.9 9 5.2 7.4c-.4-.9-.2-1.9-.2-2.9z" fill="#1a1850"/>
        </svg>
        <svg width="16" height="16" viewBox="0 0 16 16" aria-label="email">
          <circle cx="8" cy="8" r="8" fill="#fff"/>
          <rect x="4" y="5.2" width="8" height="5.6" fill="none" stroke="#1a1850" stroke-width="1.1"/>
          <path d="M4 5.4l4 3 4-3M4 10.6l3-2.4M12 10.6l-3-2.4" fill="none" stroke="#1a1850" stroke-width="1"/>
        </svg>
        <svg width="16" height="16" viewBox="0 0 16 16" aria-label="website">
          <circle cx="8" cy="8" r="8" fill="#fff"/>
          <circle cx="8" cy="8" r="4.6" fill="none" stroke="#1a1850" stroke-width="1"/>
          <ellipse cx="8" cy="8" rx="2" ry="4.6" fill="none" stroke="#1a1850" stroke-width="0.9"/>
          <path d="M3.4 8h9.2M4 5.8h8M4 10.2h8" stroke="#1a1850" stroke-width="0.8"/>
        </svg>
      </div>
      <p class="contact__line">123 456 7890</p>
      <p class="contact__line">info@yourwebsite.com</p>
      <p class="contact__line">www.yourwebsite.com</p>
    </div>
  </section>

  <section class="card card--back">
    <div class="back-texture" role="img" aria-label="Faint repeating diagonal brand pattern across the card back"></div>
    <div class="wordmark">pexla</div>
  </section>
</main>
</body>
</html>
```